Food and Beverage Business Cards

We need business cards with logo designs for a consultant in the food and beverage industry. We specialize in helping restaurants fix operational and management problems.
Specific areas of expertise include:
-Steps of service
-Staff management tools
-Standard operating procedures
-Profit and loss management
-Inventory
-Point of sales
-Bar Menu
-Mystery shopper service
-Handling and managing suppliers

Target Market(s)

Restaurant and bar owners and managers

Industry/Entity Type

Business

Contact Information for Business Card

Mathieu Girardot
Q&T Consulting
phone: 15027390614
mathqt@sampleinbox.com

Font styles to use
Other font styles liked:
• Check out the screen shot font idea

Colors

Designer to choose colors to be used in the design.

Requirements
Must have
• Must include QR code (See attachment)
• Logo should reflect our specific focus on the drinks side of the industry.
• Areas of Expertise:
• -Service Steps
• -Staff management tools
• -S.O.P
• -P&L Management
• -Inventory
• -P.O.S
• -Bar Menu
• -Mystery Shopper Service
• -Handling and Managing Suppliers

```html
<!DOCTYPE html>
<html lang="en">
<head>
<meta charset="utf-8">
<title>Q&amp;T Consulting – Business Cards</title>
<link href="https://fonts.googleapis.com/css2?family=Open+Sans:wght@400;600;700&display=swap" rel="stylesheet">
<style>
  :root {
    --backdrop: #3b3b3b;
    --card-dark: #0d0d0d;
    --card-light: #f7f7f7;
    --ink-light: #ffffff;
    --ink-dark: #1a1a1a;
    --ink-muted: #5a5a5a;
    --badge-green: #3f7a3a;
    --badge-grey: #e6e6e6;
    --rule: #2a2a2a;
  }
  * { margin: 0; padding: 0; box-sizing: border-box; }
  html, body { width: 1200px; height: 840px; overflow: hidden; }
  body {
    background: var(--backdrop);
    font-family: "Open Sans", Arial, sans-serif;
    display: flex;
    flex-direction: column;
    align-items: center;
    justify-content: center;
    gap: 44px;
  }
  .card {
    position: relative;
    width: 600px;
    height: 343px;
    box-shadow: 0 10px 28px rgba(0,0,0,0.45);
  }
  /* Front: areas of expertise */
  .card--expertise {
    background: var(--card-dark);
    color: var(--ink-light);
    text-align: center;
  }
  .badges {
    position: absolute;
    top: 26px;
    right: 30px;
    display: flex;
    gap: 8px;
  }
  .badge {
    width: 44px;
    height: 44px;
    border-radius: 50%;
    background: var(--badge-grey);
  }
  .badge--green { background: var(--badge-green); }
  .wordmark {
    font-weight: 700;
    line-height: 1;
    letter-spacing: 1px;
  }
  .card--expertise .wordmark {
    position: absolute;
    top: 108px;
    left: 0;
    right: 0;
    font-size: 52px;
    color: var(--ink-light);
  }
  .expertise-title {
    position: absolute;
    top: 182px;
    left: 0;
    right: 0;
    font-weight: 700;
    font-size: 17px;
  }
  .expertise-list {
    position: absolute;
    top: 212px;
    left: 30px;
    right: 30px;
    font-size: 14.5px;
    line-height: 1.45;
    list-style: none;
  }
  /* Back: contact */
  .card--contact {
    background: var(--card-light);
    color: var(--ink-dark);
  }
  .card--contact .wordmark {
    position: absolute;
    left: 50px;
    top: 140px;
    font-size: 50px;
    color: var(--ink-dark);
  }
  .contact {
    position: absolute;
    left: 372px;
    top: 126px;
    width: 200px;
  }
  .contact-name {
    font-weight: 700;
    font-size: 16px;
    text-transform: uppercase;
    letter-spacing: 0.2px;
  }
  .contact-role {
    font-size: 13px;
    color: var(--ink-muted);
    text-transform: uppercase;
    padding-bottom: 6px;
    border-bottom: 1.5px solid var(--rule);
    margin-bottom: 8px;
  }
  .contact-line {
    display: flex;
    align-items: center;
    gap: 8px;
    font-size: 13px;
    color: var(--ink-muted);
    line-height: 1.55;
    white-space: nowrap;
  }
  .contact-line svg { width: 12px; height: 12px; fill: var(--ink-dark); flex: none; }
</style>
</head>
<body>
  <section class="card card--expertise">
    <div class="badges">
      <span class="badge badge--green"></span>
      <span class="badge"></span>
      <span class="badge"></span>
    </div>
    <div class="wordmark">Q&amp;T Atlanta</div>
    <h2 class="expertise-title">Areas of Expertise</h2>
    <ul class="expertise-list">
      <li>Service Steps | Staff management tools | S.O.P | P&amp;L Management</li>
      <li>Inventory | P.O.S | Bar Menu | Mystery Shopper Service</li>
      <li>Handling and Managing Suppliers</li>
    </ul>
  </section>

  <section class="card card--contact">
    <div class="wordmark">Q&amp;T Atlanta</div>
    <div class="contact">
      <p class="contact-name">Mathieu Girardot</p>
      <p class="contact-role">Q&amp;T Consulting</p>
      <p class="contact-line">
        <svg viewBox="0 0 24 24" aria-hidden="true"><path d="M6.6 10.8a15.1 15.1 0 0 0 6.6 6.6l2.2-2.2a1 1 0 0 1 1-.25 11.4 11.4 0 0 0 3.6.57 1 1 0 0 1 1 1V20a1 1 0 0 1-1 1A17 17 0 0 1 3 4a1 1 0 0 1 1-1h3.5a1 1 0 0 1 1 1c0 1.25.2 2.45.57 3.57a1 1 0 0 1-.25 1z"/></svg>
        15027390614
      </p>
      <p class="contact-line">
        <svg viewBox="0 0 24 24" aria-hidden="true"><path d="M2 5h20v14H2z M2 5l10 8 10-8" /></svg>
        mathqt@sampleinbox.com
      </p>
    </div>
  </section>
</body>
</html>
```